Verodex business card

Business card for sustainable investment company called "Verodex". Verodex is an exchange platform selling carbon credits between buyers and sellers. Carbon Credits are an environmental commodity for reducing global carbon emissions.

the card should obviously have our logo and the theme should be sustainability/environment mixed with a trading platform.

Contact Information for Business Card

Logo, Name, Title, Phone, Email

Colors
0054AA
0677BA
7BADD7
CADEEF
E8F1F8
0094D4
00A9DD
6FCCEA
C7EBF8
E9F6FB
00AB8E
00BBA5
67D7C9
C6EFE9
E9F9F6
59FF00
82FF00
B8FF75
E3FFCB
F4FFEA

```html
<!DOCTYPE html>
<html lang="en">
<head>
<meta charset="utf-8">
<title>Verodex business card</title>
<link rel="stylesheet" href="https://fonts.googleapis.com/css2?family=Inter:wght@400;600;700&display=swap">
<style>
  :root {
    --backdrop: #969696;
    --card-light: #ececec;
    --card-dark: #0d2850;
    --navy-text: #12305a;
    --muted-text: #8a8a8a;
    --contact-text: #7b7b7b;
    --brand-blue: #2389fe;
    --brand-cyan: #33e3ec;
  }
  * { margin: 0; padding: 0; box-sizing: border-box; }
  html, body {
    width: 1200px; height: 1000px; overflow: hidden;
    background: var(--backdrop);
    font-family: "Inter", Arial, sans-serif;
  }
  .canvas { position: relative; width: 1200px; height: 1000px; }
  .card {
    position: absolute; width: 615px; height: 351px;
    border-radius: 28px; overflow: hidden;
  }
  .card--front { left: 287px; top: 164px; background: var(--card-light); }
  .card--back { left: 286px; top: 576px; background: var(--card-dark); }

  .brand {
    position: absolute; left: 0; right: 0; top: 62px;
    display: flex; justify-content: center; align-items: center; gap: 18px;
  }
  .brand__mark {
    width: 44px; height: 44px; border-radius: 50%;
    background: var(--brand-blue);
  }
  .brand__name {
    font-weight: 700; font-size: 38px; letter-spacing: 0.5px;
    color: var(--navy-text); line-height: 1;
  }

  .person {
    position: absolute; right: 339px; top: 191px; text-align: right;
  }
  .person__name { font-weight: 700; font-size: 17px; color: var(--navy-text); letter-spacing: 0.3px; }
  .person__title { font-size: 17px; color: var(--muted-text); margin-top: 2px; letter-spacing: 0.3px; }

  .contacts {
    position: absolute; left: 310px; top: 180px; list-style: none;
  }
  .contacts__item {
    display: flex; align-items: center; gap: 13px;
    height: 23px; font-size: 16px; color: var(--contact-text); letter-spacing: 0.6px;
  }
  .contacts__icon { width: 15px; height: 15px; flex: none; }

  .back-name {
    position: absolute; inset: 0;
    display: flex; align-items: center; justify-content: center;
    font-weight: 700; font-size: 96px; letter-spacing: 2px;
    color: var(--brand-blue);
  }
</style>
</head>
<body>
<main class="canvas">
  <section class="card card--front" aria-label="Card front">
    <div class="brand">
      <span class="brand__mark" aria-hidden="true"></span>
      <span class="brand__name">VERODEX</span>
    </div>

    <div class="person">
      <p class="person__name">Name Surname</p>
      <p class="person__title">Title</p>
    </div>

    <ul class="contacts">
      <li class="contacts__item">
        <svg class="contacts__icon" viewBox="0 0 16 16" aria-hidden="true">
          <path d="M3.5 1.5l2.5 0 1 3.5-1.6 1.2c.9 1.8 2.3 3.2 4.1 4.1L10.7 8.7l3.5 1v2.5c0 .8-.7 1.5-1.5 1.5C7 13.7 2 8.7 2 3c0-.8.7-1.5 1.5-1.5z" fill="var(--brand-blue)"/>
        </svg>
        <span>012•345•6789</span>
      </li>
      <li class="contacts__item">
        <svg class="contacts__icon" viewBox="0 0 16 16" aria-hidden="true">
          <rect x="1" y="3" width="14" height="10" rx="1" fill="var(--brand-blue)"/>
          <path d="M1.5 3.5L8 9l6.5-5.5" fill="none" stroke="#fff" stroke-width="1.2"/>
        </svg>
        <span>name@website.com</span>
      </li>
      <li class="contacts__item">
        <svg class="contacts__icon" viewBox="0 0 16 16" aria-hidden="true">
          <g fill="none" stroke="var(--brand-blue)" stroke-width="1.1">
            <circle cx="8" cy="8" r="6.5"/>
            <ellipse cx="8" cy="8" rx="3" ry="6.5"/>
            <path d="M1.5 8h13M2.5 4.8h11M2.5 11.2h11"/>
          </g>
        </svg>
        <span>website.com</span>
      </li>
    </ul>
  </section>

  <section class="card card--back" aria-label="Card back">
    <div class="back-name">VERODEX</div>
  </section>
</main>
</body>
</html>
```